2022 Yearly Patron Drive (art gallery annual report)

6X9, 16-page brochure that serves both as an annual report for the previous year and gets mailed for an ask for donations. This must be done in InDesign and I will provide a template. I am also sending PDFs for the previous two years. Last year was pink and black, but I have recolored the logo purple this year.. so am open to whatever colors. I used last year's template to put in the new info. The theme for this year is Amazing - last year was Thriving. The font I chose for the front I do not want to use.. its just an example. All three pictures on the front don't have to be used.. just ideas.
Updates

I put three photos on the front page. It isn't necessary to use all of them, I thought there might be something there to use as part of the design

The current information is in the InDesign file, Calatalog Design.indd with the to Links Folders attached.

Target Market(s)

Donors

Industry/Entity Type

Art

Font styles to use
Sans Serif

Requirements
Must have
• InDesign
Nice to have
• A new look! Something different than 2021 an 2020 (PDFs included)

```html
<!DOCTYPE html>
<html lang="en">
<head>
<meta charset="utf-8">
<title>The Arts – Meridian Gallery Annual Report</title>
<link rel="stylesheet" href="https://fonts.googleapis.com/css2?family=Bebas+Neue&family=Montserrat:wght@300;400&display=swap">
<style>
  :root {
    --purple: #8f459b;
    --ink: #231f20;
    --body: #4a4a4a;
    --paper: #ffffff;
    --c-blue: #4472c4;
    --c-orange: #ed7d31;
    --c-gray: #a5a5a5;
    --c-gold: #ffc000;
    --c-sky: #5b9bd5;
    --c-green: #70ad47;
    --c-navy: #264478;
    --c-brown: #9e480e;
  }
  * { margin: 0; padding: 0; box-sizing: border-box; }
  html, body { width: 1200px; height: 800px; overflow: hidden; background: var(--paper); }
  .page { position: relative; width: 1200px; height: 800px; overflow: hidden; font-family: 'Montserrat', sans-serif; }

  .section-band { position: absolute; left: 0; top: 71px; width: 362px; height: 87px; background: var(--purple); }
  .section-band-rule { position: absolute; left: 369px; top: 71px; width: 8px; height: 87px; background: var(--purple); }
  .section-title {
    position: absolute; left: 0; top: 71px; width: 410px; height: 87px;
    font-family: 'Bebas Neue', sans-serif; font-size: 66px; line-height: 92px;
    color: var(--paper); text-align: center; letter-spacing: 0.5px;
  }

  .brand-name {
    position: absolute; left: 836px; top: 70px; width: 320px;
    font-family: 'Bebas Neue', sans-serif; font-size: 88px; line-height: 88px;
    color: var(--ink); letter-spacing: 6px; text-align: right;
  }

  .portrait {
    position: absolute; left: 112px; top: 211px; width: 239px; height: 310px;
    background: linear-gradient(160deg, #b8c4a8 0%, #d9dcd6 30%, #6d6468 60%, #3b3438 100%);
  }
  .frame-corner { position: absolute; border-color: var(--purple); border-style: solid; }
  .frame-corner.top-left { left: 105px; top: 204px; width: 58px; height: 61px; border-width: 2px 0 0 2px; }
  .frame-corner.bottom-right { left: 300px; top: 467px; width: 59px; height: 61px; border-width: 0 2px 2px 0; }
  .portrait-caption {
    position: absolute; left: 112px; top: 540px; width: 239px; text-align: center;
    font-family: 'Bebas Neue', sans-serif; font-size: 28px; line-height: 34px; color: var(--purple);
  }

  .letter { position: absolute; left: 390px; top: 209px; width: 685px; color: var(--body); }
  .letter p { font-weight: 300; font-size: 17.4px; line-height: 22.2px; text-align: justify; margin-bottom: 15px; }

  .tagline {
    position: absolute; left: 1107px; top: 612px; width: 400px;
    transform-origin: 0 0; transform: rotate(-90deg);
    font-family: 'Bebas Neue', sans-serif; font-size: 50px; line-height: 40px;
    color: var(--purple); white-space: nowrap;
  }
  .side-rule { position: absolute; left: 1083px; top: 629px; width: 87px; height: 6px; background: var(--purple); }
  .side-block { position: absolute; left: 1083px; top: 643px; width: 87px; height: 157px; background: var(--purple); }

  .folio-band { position: absolute; left: 0; top: 741px; width: 61px; height: 19px; background: var(--purple); }
  .folio-number { position: absolute; left: 44px; top: 741px; font-size: 11px; line-height: 19px; color: var(--paper); font-weight: 400; }
  .folio-rule { position: absolute; left: 65px; top: 741px; width: 3px; height: 19px; background: var(--purple); }
  .theme-word {
    position: absolute; left: 78px; top: 727px;
    font-family: 'Bebas Neue', sans-serif; font-size: 52px; line-height: 52px; color: var(--purple);
  }

  .chart-title {
    position: absolute; width: 200px; text-align: center;
    font-size: 17px; font-weight: 400; color: #595959; letter-spacing: 0.5px;
  }
  .chart-title.expenses { left: 445px; top: 540px; }
  .chart-title.income { left: 773px; top: 536px; }
  .pie { position: absolute; }
  .pie.expenses { left: 489px; top: 567px; }
  .pie.income { left: 814px; top: 566px; }

  .legend { position: absolute; list-style: none; font-size: 9.6px; color: #595959; }
  .legend li { position: absolute; white-space: nowrap; }
  .legend li::before { content: ""; display: inline-block; width: 4px; height: 4px; margin-right: 3px; vertical-align: 1px; background: var(--swatch); }
</style>
</head>
<body>
<main class="page">
  <div class="section-band"></div>
  <div class="section-band-rule"></div>
  <h1 class="section-title">The Arts</h1>

  <div class="brand-name">MERIDIAN</div>

  <div class="frame-corner top-left"></div>
  <div class="portrait" role="img" aria-label="Portrait photo of the gallery director on a porch"></div>
  <div class="frame-corner bottom-right"></div>
  <p class="portrait-caption">Owen Carrick, Director</p>

  <section class="letter">
    <p>The Meridian Gallery Guild extends our appreciation to the entire community this past year as we continue to Cultivate a Love of Art.</p>
    <p>Our deepest gratitude to all who continued to keep the visual arts alive through our exhibits at Meridian Gallery, The Lantern Hall, and Hotel Verano. Plus being part of the Arts Commission and its work helps to extend our mission to provide a visual arts experience for the community.</p>
    <p>We also partner with visual and performance arts organizations such as the Crescent Theatre, Willow Creek Arts, Ashford Symphony Orchestra, Ashford Valley Museum, Ashford Town Hall, Ashford Maker Space, and The Lantern Hall.</p>
    <p>It is the mission of the Meridian Gallery to foster curiosity and appreciation for the visual arts in our diverse community.</p>
  </section>

  <div class="chart-title expenses">EXPENSES</div>
  <svg class="pie expenses" width="104" height="104" viewBox="0 0 104 104" role="img" aria-label="Expenses pie chart">
    <g transform="rotate(-90 52 52)" fill="none" stroke-width="51">
      <circle cx="52" cy="52" r="25.5" pathLength="100" stroke="var(--c-blue)" stroke-dasharray="11 100" stroke-dashoffset="0"/>
      <circle cx="52" cy="52" r="25.5" pathLength="100" stroke="var(--c-orange)" stroke-dasharray="20 100" stroke-dashoffset="-11"/>
      <circle cx="52" cy="52" r="25.5" pathLength="100" stroke="var(--c-gray)" stroke-dasharray="5 100" stroke-dashoffset="-31"/>
      <circle cx="52" cy="52" r="25.5" pathLength="100" stroke="var(--c-gold)" stroke-dasharray="4 100" stroke-dashoffset="-36"/>
      <circle cx="52" cy="52" r="25.5" pathLength="100" stroke="var(--c-sky)" stroke-dasharray="1.5 100" stroke-dashoffset="-40"/>
      <circle cx="52" cy="52" r="25.5" pathLength="100" stroke="var(--c-green)" stroke-dasharray="3 100" stroke-dashoffset="-41.5"/>
      <circle cx="52" cy="52" r="25.5" pathLength="100" stroke="var(--c-navy)" stroke-dasharray="34 100" stroke-dashoffset="-44.5"/>
      <circle cx="52" cy="52" r="25.5" pathLength="100" stroke="var(--c-brown)" stroke-dasharray="21.5 100" stroke-dashoffset="-78.5"/>
    </g>
  </svg>
  <ul class="legend">
    <li style="left:404px;top:682px;--swatch:var(--c-blue)">Special Events</li>
    <li style="left:484px;top:682px;--swatch:var(--c-orange)">Exhibitions</li>
    <li style="left:557px;top:682px;--swatch:var(--c-gray)">Publicity</li>
    <li style="left:629px;top:682px;--swatch:var(--c-gold)">Membership</li>
    <li style="left:404px;top:701px;--swatch:var(--c-sky)">Collection</li>
    <li style="left:484px;top:701px;--swatch:var(--c-green)">Giftshop</li>
    <li style="left:557px;top:701px;--swatch:var(--c-navy)">Staff</li>
    <li style="left:629px;top:701px;--swatch:var(--c-brown)">Operations</li>
  </ul>

  <div class="chart-title income">INCOME</div>
  <svg class="pie income" width="106" height="106" viewBox="0 0 106 106" role="img" aria-label="Income pie chart">
    <g transform="rotate(-90 53 53)" fill="none" stroke-width="52">
      <circle cx="53" cy="53" r="26" pathLength="100" stroke="var(--c-blue)" stroke-dasharray="25 100" stroke-dashoffset="0"/>
      <circle cx="53" cy="53" r="26" pathLength="100" stroke="var(--c-orange)" stroke-dasharray="22 100" stroke-dashoffset="-25"/>
      <circle cx="53" cy="53" r="26" pathLength="100" stroke="var(--c-gray)" stroke-dasharray="3 100" stroke-dashoffset="-47"/>
      <circle cx="53" cy="53" r="26" pathLength="100" stroke="var(--c-gold)" stroke-dasharray="20 100" stroke-dashoffset="-50"/>
      <circle cx="53" cy="53" r="26" pathLength="100" stroke="var(--c-sky)" stroke-dasharray="14 100" stroke-dashoffset="-70"/>
      <circle cx="53" cy="53" r="26" pathLength="100" stroke="var(--c-green)" stroke-dasharray="16 100" stroke-dashoffset="-84"/>
    </g>
  </svg>
  <ul class="legend">
    <li style="left:751px;top:679px;--swatch:var(--c-blue)">Individual Contributions</li>
    <li style="left:880px;top:679px;--swatch:var(--c-orange)">Grants</li>
    <li style="left:964px;top:679px;--swatch:var(--c-gray)">Gift Shop</li>
    <li style="left:751px;top:696px;--swatch:var(--c-gold)">Membership</li>
    <li style="left:880px;top:696px;--swatch:var(--c-sky)">Special Events</li>
    <li style="left:964px;top:696px;--swatch:var(--c-green)">Exhibitions</li>
  </ul>

  <div class="tagline">Cultivating a Love of Art</div>
  <div class="side-rule"></div>
  <div class="side-block"></div>

  <div class="folio-band"></div>
  <span class="folio-number">2</span>
  <div class="folio-rule"></div>
  <div class="theme-word">AMAZING</div>
</main>
</body>
</html>
```